International Clinical Software Company needs a new business card design

We are looking for a new business card design for our company that has recently expanded into the UK market, making us a multinational company.
After having rebranded our website and produced a new style guide, we are looking for a business card that is creative and attention grabbing, while being consistent with the style and colour scheme used on the new website, www.plumvora.example
We produce care management technology for the aged care market, but the main aspect we aim to communicate is the human element of our software, and the way it assists in providing better care for aged people, and stronger relationships between aged people and the staff that care for them.
Our current business card is a dark green with gold text, which makes the text quite difficult to read, not very aesthetically appealing and the colour scheme looks quite dated.
We would like something fresh and modern, that can still be colourful but doesn't use large blocks of dark colour, and uses the colours within our logo.
Something tying in with the leaves that are used in our logo could work quite nicely, along with the Autumn/Fall colours of soft greens, yellows and reds (also in our existing logo). However also happy to look at fresh, completely out of the box ideas we may not have yet considered.
Target Market(s)
The people that receive this business card work in the aged card or health industry and are either corporate/management level staff or clinical (Registered Nurses, care workers etc.)
Industry/Entity Type
Health Product
Contact Information for Business Card
Company Name - BrindlewayCare
Company locations: United Kingdom, Australia, New Zealand
Staff Details:
Staff name: Derek Mallow
Staff job title: Executive Chairman
Staff email: d.mallow@plumvora.example
Office phone number: 01742 918576
Font styles to use
Other font styles liked:
- Calibri
Requirements
Must have
- Must include the BrindlewayCare brand name in it's current font
- Must include logo (3 leaves in gold circle)
- Must include Business Card Details
Nice to have
- Elements of gold
- White space
- Something autumn themed but not too cliched
Should not have
- No blue - used by a major competitor and we would like to differentiate from them
- Large blocks of dark green colour (the green that appears in our leaves on the logo on our current business card is the background colour and it is far too dark)

```html
<!DOCTYPE html>
<html lang="en">
<head>
<meta charset="utf-8">
<title>BrindlewayCare – Business Card</title>
<link rel="stylesheet" href="https://fonts.googleapis.com/css2?family=Source+Sans+3:wght@300;400;600&display=swap">
<style>
  :root {
    --backdrop: #7f8080;
    --card: #f2f2f4;
    --gold: #a38f66;
    --gold-band: #a08d68;
    --crimson: #a3143f;
    --leaf-yellow: #d4b73a;
    --leaf-green: #55782f;
    --ink: #4a4a4c;
    --icon: #8a7d62;
    --rule: #b9b9b9;
    --white: #ffffff;
  }
  * { box-sizing: border-box; margin: 0; padding: 0; }
  html, body {
    width: 1105px;
    height: 1200px;
    overflow: hidden;
    background: var(--backdrop);
    font-family: "Source Sans 3", Calibri, Arial, sans-serif;
  }
  .business-card {
    position: absolute;
    left: 80px;
    top: 330px;
    width: 945px;
    height: 540px;
    background: var(--card);
    overflow: hidden;
  }
  .brand {
    position: absolute;
    left: 230px;
    top: 94px;
    display: flex;
    align-items: center;
    gap: 22px;
  }
  .brand-mark {
    width: 164px;
    height: 164px;
    border-radius: 50%;
    border: 5px solid var(--gold);
  }
  .brand-name {
    font-weight: 300;
    font-size: 54px;
    color: var(--gold);
    letter-spacing: 0.5px;
  }
  .person {
    position: absolute;
    right: calc(945px - 409px);
    top: 318px;
    text-align: right;
  }
  .person-name {
    font-weight: 600;
    font-size: 33px;
    color: var(--gold);
    line-height: 40px;
  }
  .person-title {
    font-weight: 400;
    font-size: 26px;
    color: var(--crimson);
    line-height: 36px;
  }
  .divider {
    position: absolute;
    left: 444px;
    top: 304px;
    width: 2px;
    height: 101px;
    background: var(--rule);
  }
  .contact-list {
    position: absolute;
    left: 490px;
    top: 302px;
    list-style: none;
  }
  .contact-item {
    display: flex;
    align-items: center;
    gap: 9px;
    height: 37px;
    font-size: 24px;
    color: var(--ink);
  }
  .contact-icon { width: 20px; height: 20px; flex: none; fill: var(--icon); }
  .accent-rules {
    position: absolute;
    left: 0;
    top: 483px;
    width: 945px;
    height: 3px;
    display: flex;
    gap: 3px;
  }
  .accent-rules span { flex: 1; }
  .rule-red { background: var(--crimson); }
  .rule-yellow { background: var(--leaf-yellow); }
  .rule-green { background: var(--leaf-green); }
  .locations-band {
    position: absolute;
    left: 0;
    top: 491px;
    width: 945px;
    height: 49px;
    background: var(--gold-band);
    color: var(--white);
    font-size: 26px;
    line-height: 49px;
    text-align: center;
    padding-right: 0;
  }
  .locations-band .sep { margin: 0 6px; }
</style>
</head>
<body>
  <div class="business-card">
    <div class="brand">
      <div class="brand-mark"></div>
      <div class="brand-name">BrindlewayCare</div>
    </div>

    <div class="person">
      <div class="person-name">Derek Mallow</div>
      <div class="person-title">Executive Chairman</div>
    </div>

    <div class="divider"></div>

    <ul class="contact-list">
      <li class="contact-item">
        <svg class="contact-icon" viewBox="0 0 24 24" aria-hidden="true"><path d="M6.6 10.8a15.1 15.1 0 0 0 6.6 6.6l2.2-2.2a1 1 0 0 1 1-.25 11.4 11.4 0 0 0 3.6.57 1 1 0 0 1 1 1V20a1 1 0 0 1-1 1A17 17 0 0 1 3 4a1 1 0 0 1 1-1h3.5a1 1 0 0 1 1 1c0 1.25.2 2.45.57 3.57a1 1 0 0 1-.25 1z"/></svg>
        <span>01742 918576</span>
      </li>
      <li class="contact-item">
        <svg class="contact-icon" viewBox="0 0 24 24" aria-hidden="true"><path d="M2 5h20v14H2z M3.5 6.5 12 13l8.5-6.5" fill="var(--icon)"/><path d="M3 6l9 7 9-7" fill="none" stroke="var(--card)" stroke-width="1.6"/></svg>
        <span>d.mallow@plumvora.example</span>
      </li>
      <li class="contact-item">
        <svg class="contact-icon" viewBox="0 0 24 24" aria-hidden="true"><circle cx="12" cy="12" r="10"/><path d="M12 2v20M2 12h20M12 2c-4 4-4 16 0 20M12 2c4 4 4 16 0 20" fill="none" stroke="var(--card)" stroke-width="1.3"/></svg>
        <span>www.plumvora.example</span>
      </li>
    </ul>

    <div class="accent-rules">
      <span class="rule-red"></span>
      <span class="rule-yellow"></span>
      <span class="rule-green"></span>
    </div>

    <div class="locations-band">
      United Kingdom<span class="sep">|</span>Australia<span class="sep">|</span> New Zealand
    </div>
  </div>
</body>
</html>
```